New Business Card Design Project

Need a design that will create an impact / strong impression towards our clients for our business. We are in the lighting business and we do lighting retrofits for large commercial to industrial clientele.

Target Market(s)

Lighting Industry

Industry/Entity Type

Business

Font styles to use
Other font styles liked:
• we would like to use the font on our logo, not sure what it is though..

Requirements
Must have
• Our logo.
Nice to have
• We are open to suggestions that have to do with lighting.

```html
<!DOCTYPE html>
<html lang="en">
<head>
<meta charset="utf-8">
<title>Keystone Volt Lighting – Business Card</title>
<link rel="stylesheet" href="https://fonts.googleapis.com/css2?family=Roboto+Condensed:wght@400;700&display=swap">
<style>
  :root {
    --backdrop: #ecebe6;
    --card-white: #f7f7f5;
    --forest: #1f5e22;
    --forest-deep: #174a1a;
    --leaf: #4fae3f;
    --lime: #65c455;
    --ink: #4a4a4a;
    --rule: #cfcfcf;
    --white: #ffffff;
  }
  * { box-sizing: border-box; margin: 0; padding: 0; }
  html, body { width: 1200px; height: 911px; overflow: hidden; }
  body {
    background: var(--backdrop);
    font-family: "Roboto Condensed", "Arial Narrow", sans-serif;
    position: relative;
  }
  .card {
    position: absolute;
    top: 300px;
    width: 540px;
    height: 310px;
    border-radius: 22px;
    overflow: hidden;
    box-shadow: 0 10px 28px rgba(0,0,0,0.18);
  }
  /* Front */
  .card-front { left: 40px; background: var(--card-white); }
  .front-brand {
    position: absolute; left: 0; top: 0; width: 270px; height: 250px;
    display: flex; align-items: center; justify-content: center; gap: 10px;
  }
  .brand-mark { width: 16px; height: 16px; background: var(--forest); }
  .brand-name {
    font-weight: 700; font-size: 25px; color: var(--forest);
    letter-spacing: 0.5px; text-transform: uppercase; line-height: 1.05;
  }
  .front-divider {
    position: absolute; left: 270px; top: 26px; width: 1px; height: 200px;
    background: var(--rule);
  }
  .front-details { position: absolute; left: 300px; top: 32px; color: var(--ink); }
  .person-name { font-weight: 700; font-size: 26px; color: var(--forest); letter-spacing: 0.3px; }
  .person-role { font-weight: 700; font-size: 16px; color: var(--leaf); margin-top: 1px; }
  .address { font-size: 15px; margin-top: 14px; line-height: 1.25; }
  .contact-list { list-style: none; margin-top: 10px; font-size: 15px; line-height: 1.3; }
  .contact-list li { display: flex; align-items: center; gap: 8px; }
  .contact-list svg { width: 12px; height: 12px; fill: var(--ink); flex: none; }
  .front-band {
    position: absolute; left: 0; bottom: 0; width: 100%; height: 60px;
    background: linear-gradient(90deg, var(--forest-deep), var(--forest));
    display: flex; align-items: center; justify-content: flex-end; padding-right: 38px;
  }
  .band-web { color: var(--white); font-weight: 700; font-size: 15px; letter-spacing: 2.5px; }
  /* Back */
  .card-back { left: 620px; background: var(--lime); }
  .back-brand {
    position: absolute; inset: 0 0 60px 0;
    display: flex; align-items: center; justify-content: center; gap: 14px;
  }
  .back-brand .brand-mark { width: 20px; height: 20px; background: var(--white); }
  .back-brand .brand-name { color: var(--white); font-size: 36px; }
  .back-web {
    position: absolute; left: 0; right: 0; bottom: 38px; text-align: center;
    color: var(--white); font-size: 15px; letter-spacing: 3px;
  }
</style>
</head>
<body>
  <section class="card card-front" aria-label="Business card front">
    <div class="front-brand">
      <span class="brand-mark"></span>
      <span class="brand-name">Keystone Volt<br>Lighting</span>
    </div>
    <div class="front-divider"></div>
    <div class="front-details">
      <p class="person-name">DANIEL REYES</p>
      <p class="person-role">CEO/FOUNDER</p>
      <p class="address">2140 Birchwood Road<br>Fairbanks, Alaska 99701</p>
      <ul class="contact-list">
        <li><svg viewBox="0 0 12 12"><path d="M2 1h3l1 3-2 1a6 6 0 0 0 3 3l1-2 3 1v3c-6 1-10-3-9-9z"/></svg>555 210 4478</li>
        <li><svg viewBox="0 0 12 12"><path d="M3 0h6v12H3zM4 1.5v8h4v-8z"/></svg>555 318 2290</li>
        <li><svg viewBox="0 0 12 12"><path d="M3 0h6v3H3zM1 4h10v6H9v2H3v-2H1zM4 8v3h4V8z"/></svg>555 604 7713</li>
        <li><svg viewBox="0 0 12 12"><path d="M0 2h12v8H0zM1 3l5 4 5-4z" fill-rule="evenodd"/></svg>daniel@keystonevolt.com</li>
      </ul>
    </div>
    <div class="front-band"><span class="band-web">www.keystonevoltlighting.com</span></div>
  </section>

  <section class="card card-back" aria-label="Business card back">
    <div class="back-brand">
      <span class="brand-mark"></span>
      <span class="brand-name">Keystone Volt Lighting</span>
    </div>
    <p class="back-web">www.keystonevoltlighting.com</p>
  </section>
</body>
</html>
```